RW Framewell Inc Business cards

We need business cards using our existing logo but slightly modified. Right now the logo says RW Loadbearing Masonry. We want to keep the RW part of the design, but replace the Structural Concrete portion with "FRAMEWELL". Please see the attached file.
Ideally this would be a blank template so we can add Different Names, titles, and phone numbers later.
On the one side we want only the logo and on the other side the detail. I'm attaching an example for you to see.
Please reach out with any other questions. Our address and other details will be given out once we find a design we like.

Target Market(s)

Construction Industry

```html
<!DOCTYPE html>
<html lang="en">
<head>
<meta charset="utf-8">
<title>RW Framewell Inc – Business Cards</title>
<link href="https://fonts.googleapis.com/css2?family=Montserrat:wght@700&family=Roboto:wght@400;700&display=swap" rel="stylesheet">
<style>
  :root {
    --backdrop: #3b3b3d;
    --card: #1f1f21;
    --brand-blue: #2f66ad;
    --strip-grey: #7d7d80;
    --text-light: #f2f2f2;
    --watermark: #29292c;
  }
  * { margin: 0; padding: 0; box-sizing: border-box; }
  html, body { width: 799px; height: 1200px; overflow: hidden; }
  body {
    background: var(--backdrop);
    font-family: "Roboto", Arial, sans-serif;
    color: var(--text-light);
    position: relative;
  }
  .card {
    position: absolute;
    left: 80px;
    width: 640px;
    height: 366px;
    background: var(--card);
    border-radius: 4px;
    overflow: hidden;
    box-shadow: 0 10px 28px rgba(0,0,0,0.45);
  }
  .card--front { top: 117px; }
  .card--back { top: 717px; }

  .wordmark {
    position: absolute;
    font-family: "Montserrat", Arial, sans-serif;
    font-weight: 700;
    color: var(--brand-blue);
    display: flex;
    align-items: center;
    gap: 14px;
  }
  .wordmark__square { background: var(--brand-blue); flex: none; }
  .wordmark__lines { display: flex; flex-direction: column; line-height: 1; }

  .card--front .wordmark { left: 50%; top: 50%; transform: translate(-50%, -50%); }
  .card--front .wordmark__square { width: 26px; height: 26px; }
  .card--front .wordmark__initials { font-size: 96px; letter-spacing: 2px; }
  .card--front .wordmark__name { font-size: 34px; letter-spacing: 9px; margin-top: 6px; }

  .card--back .wordmark { left: 40px; top: 30px; gap: 10px; }
  .card--back .wordmark__square { width: 16px; height: 16px; }
  .card--back .wordmark__initials { font-size: 62px; letter-spacing: 1px; }
  .card--back .wordmark__name { font-size: 22px; letter-spacing: 6px; margin-top: 4px; }

  .watermark {
    position: absolute;
    right: 20px;
    top: 120px;
    font-family: "Montserrat", Arial, sans-serif;
    font-weight: 700;
    font-size: 170px;
    line-height: 1;
    color: var(--watermark);
  }

  .holder { position: absolute; left: 40px; top: 188px; }
  .holder__name { font-size: 22px; font-weight: 700; color: var(--brand-blue); }
  .holder__title { font-size: 14px; margin-top: 4px; }

  .contact {
    position: absolute;
    left: 330px;
    top: 186px;
    font-size: 15px;
    line-height: 1.45;
    list-style: none;
  }
  .contact__item { display: flex; align-items: center; gap: 10px; }
  .contact__item svg { width: 14px; height: 14px; fill: var(--brand-blue); flex: none; }
  .contact__address { margin-top: 4px; }

  .strip {
    position: absolute;
    left: 0;
    top: 290px;
    width: 280px;
    height: 10px;
    background: var(--strip-grey);
  }
  .band {
    position: absolute;
    left: 250px;
    right: 0;
    top: 290px;
    bottom: 0;
    background: var(--brand-blue);
    border-top-left-radius: 34px;
    display: flex;
    align-items: center;
    justify-content: flex-end;
    padding-right: 40px;
  }
  .band__site { font-size: 19px; font-weight: 700; color: #fff; }
</style>
</head>
<body>

<section class="card card--front" aria-label="Card front">
  <div class="wordmark">
    <span class="wordmark__square"></span>
    <span class="wordmark__lines">
      <span class="wordmark__initials">RW</span>
      <span class="wordmark__name">FRAMEWELL</span>
    </span>
  </div>
</section>

<section class="card card--back" aria-label="Card back">
  <div class="watermark" aria-hidden="true">RW</div>

  <div class="wordmark">
    <span class="wordmark__square"></span>
    <span class="wordmark__lines">
      <span class="wordmark__initials">RW</span>
      <span class="wordmark__name">FRAMEWELL</span>
    </span>
  </div>

  <div class="holder">
    <p class="holder__name">Dale RW Porter</p>
    <p class="holder__title">Managing Director</p>
  </div>

  <ul class="contact">
    <li class="contact__item">
      <svg viewBox="0 0 24 24" aria-hidden="true"><path d="M6.6 10.8a15.1 15.1 0 0 0 6.6 6.6l2.2-2.2a1 1 0 0 1 1-.25 11.4 11.4 0 0 0 3.6.57 1 1 0 0 1 1 1V20a1 1 0 0 1-1 1A17 17 0 0 1 3 4a1 1 0 0 1 1-1h3.5a1 1 0 0 1 1 1c0 1.25.2 2.45.57 3.6a1 1 0 0 1-.25 1z"/></svg>
      <span>555-014-2237</span>
    </li>
    <li class="contact__item">
      <svg viewBox="0 0 24 24" aria-hidden="true"><path d="M2 5h20v14H2zm2 2v.5l8 5 8-5V7zm0 2.8V17h16V9.8l-8 5z"/></svg>
      <span>dale@framewellinc.com</span>
    </li>
    <li class="contact__address">78 Trussline Rd., Millbrook,<br>Oregon, US 970145</li>
  </ul>

  <div class="strip"></div>
  <div class="band"><span class="band__site">www.framewellinc.com</span></div>
</section>

</body>
</html>
```